TL - business card

Tallow Partners is an insurance brokerage firm, inovative, proactive, vigorous, which aims to become the leader of the insurance brokers in Anfrica. We should like to get some designs which should be avoided also in Gray / Metallic for the Administration and Orange / Blue for the Managers (ike in the picture sent). The Blue / Green logo is not the correct one, but the source of the file. Please adjust the color accordingly for the business cards. 1 / Orange / Blue 2 / Gray / Metallic We want something classic but which is transmitted strenght, inovation, modernity and most of all, rapidity. We want something start-up like, very punchy and catching eye remaining profesional at the same time. Name: Dorian Whitlock Function: Managing Director Address: N ° 17/18 Rua Veloso - R / C 2B Direita - Bairro Mutamba - Luanda Tel: (+244) 947 582 316 Email: dorian.whitlock@tallow-p.example Website: www.tallow-p. example We want classic in the front and creative, colorfull at the back. The cards will be printed in relief, with very high quality of paper.
Insurance Broker
Colors
Designer to choose colors to be used in the design.

```html
<!DOCTYPE html>
<html lang="en">
<head>
<meta charset="utf-8">
<title>Tallow Partners – Business Card</title>
<link rel="stylesheet" href="https://fonts.googleapis.com/css2?family=Lato:wght@400;700;900&family=Roboto:wght@700&display=swap">
<style>
  :root {
    --page: #e4e4e4;
    --card: #ffffff;
    --brand-blue: #0b7bc4;
    --brand-red: #e0382b;
    --brand-orange: #f39a52;
    --ink: #555555;
  }
  * { box-sizing: border-box; margin: 0; padding: 0; }
  html, body { width: 1125px; height: 1200px; overflow: hidden; }
  body {
    background: var(--page);
    font-family: "Lato", sans-serif;
    position: relative;
  }
  .card {
    position: absolute;
    left: 178px;
    width: 768px;
    height: 437px;
    border-radius: 18px;
    overflow: hidden;
  }
  .card--front { top: 140px; background: var(--card); }
  .card--back { top: 626px; background: var(--brand-blue); }

  .brand {
    position: absolute;
    left: 40px;
    width: 354px;
    top: 200px;
    display: flex;
    align-items: center;
    justify-content: center;
    gap: 10px;
  }
  .brand__dot {
    width: 16px; height: 16px; border-radius: 50%;
    background: var(--brand-orange);
  }
  .brand__name {
    font-weight: 900;
    font-size: 32px;
    color: var(--brand-blue);
    letter-spacing: 0.5px;
  }

  .divider {
    position: absolute;
    left: 383px; top: 120px;
    width: 2px; height: 196px;
    background: linear-gradient(to bottom, var(--brand-orange), var(--brand-red));
  }

  .contact { position: absolute; left: 423px; top: 110px; color: var(--ink); }
  .contact__name {
    font-family: "Roboto", sans-serif;
    font-weight: 700;
    font-size: 29px;
    color: var(--brand-blue);
    letter-spacing: 0.6px;
    line-height: 1;
  }
  .contact__role { font-size: 18px; margin-top: 11px; }
  .contact__address { font-size: 17.5px; line-height: 21px; margin-top: 14px; }
  .contact__list { list-style: none; margin-top: 15px; }
  .contact__item {
    display: flex; align-items: center;
    font-size: 18px; height: 30px;
  }
  .contact__icon { width: 14px; height: 14px; margin-left: 1px; margin-right: 11px; flex: none; }

  .rule {
    position: absolute; left: 0; right: 0; top: 409px; height: 3px;
    background: linear-gradient(to right, var(--brand-red), var(--brand-orange));
  }
  .band {
    position: absolute; left: 0; right: 0; top: 414px; bottom: 0;
    background: var(--brand-blue);
  }

  .back-pattern { position: absolute; inset: 0; background: var(--brand-blue); }
  .back-mark {
    position: absolute; left: 590px; top: 293px;
    width: 60px; text-align: center;
    font-weight: 900; font-size: 30px; color: #ffffff;
  }
</style>
</head>
<body>
  <section class="card card--front">
    <div class="brand">
      <span class="brand__dot"></span>
      <span class="brand__name">Tallow Partners</span>
    </div>
    <div class="divider"></div>
    <div class="contact">
      <h1 class="contact__name">Dorian Whitlock</h1>
      <p class="contact__role">Managing Director</p>
      <p class="contact__address">&nbsp;N ° 17/18 Rua Veloso - R / C 2B<br>Direita - Bairro Mutamba - Luanda</p>
      <ul class="contact__list">
        <li class="contact__item">
          <svg class="contact__icon" viewBox="0 0 24 24" aria-hidden="true"><path fill="#0b7bc4" d="M6.6 10.8a15 15 0 0 0 6.6 6.6l2.2-2.2c.3-.3.7-.4 1-.2 1.1.4 2.3.6 3.6.6.6 0 1 .4 1 1V20c0 .6-.4 1-1 1A17 17 0 0 1 3 4c0-.6.4-1 1-1h3.5c.6 0 1 .4 1 1 0 1.3.2 2.5.6 3.6.1.3 0 .7-.2 1z"/></svg>
          (+244) 947 582 316
        </li>
        <li class="contact__item">
          <svg class="contact__icon" viewBox="0 0 24 24" aria-hidden="true"><rect x="2" y="5" width="20" height="14" rx="1" fill="#0b7bc4"/><path d="M5 8l7 6 7-6" fill="none" stroke="#fff" stroke-width="2"/></svg>
          dorian.whitlock@tallow-p.example
        </li>
        <li class="contact__item">
          <svg class="contact__icon" viewBox="0 0 24 24" aria-hidden="true"><circle cx="12" cy="12" r="10" fill="#0b7bc4"/><path d="M7 6c2 1 3 3 2 5s1 3 2 4M15 4c-1 2 1 4 3 4M14 20c0-2 2-3 4-3" fill="none" stroke="#fff" stroke-width="1.6"/></svg>
          www.tallow-p. example
        </li>
      </ul>
    </div>
    <div class="rule"></div>
    <div class="band"></div>
  </section>

  <section class="card card--back">
    <div class="back-pattern" role="img" aria-label="Faint repeating brand pattern in a slightly lighter blue"></div>
    <div class="back-mark">TL</div>
  </section>
</body>
</html>
```